CM Candle Tube Packaging Design

Website: www.corvelmare.example
IG: @corvel.mare
Tagline: Elevate Your Ambiance
My brand is a sophisticated brand with luxury candles made of coconut wax. Im looking for an upscale minimalist chic design.
Discover the transformative power of positive energy with Corvel Mare candles. Indulge in true luxury with our specially crafted coconut wax blend that not only ignites captivating scents but also embodies modern elegance and empowering elements.
At Corvel Mare we're committed to delivering a unique and exhilarating aromatic experience to all candle lovers. Each candle is meticulously handcrafted in small batches using luxury fragrance oils exclusively formulated for coconut wax.
Our candles are:
Clean-burning
Paraben-Free
Phthalate-Free
Skin-Safe
Pet-Friendly

```html
<!DOCTYPE html>
<html lang="en">
<head>
<meta charset="utf-8">
<title>Corvel Mare — Candle Label</title>
<link rel="stylesheet" href="https://fonts.googleapis.com/css2?family=Cormorant+Garamond:wght@500&family=Great+Vibes&family=Josefin+Sans:wght@300&family=Poppins:wght@300;400&display=swap">
<style>
  :root {
    --backdrop: #434f43;
    --label: #dde2dc;
    --ink: #141a26;
    --rule: #a9b0a9;
  }
  * { margin: 0; padding: 0; box-sizing: border-box; }
  html, body { width: 1200px; height: 3000px; overflow: hidden; }
  body { background: var(--backdrop); position: relative; }

  .label {
    position: absolute;
    left: 150px;
    top: 768px;
    width: 900px;
    height: 1463px;
    background: var(--label);
    box-shadow: 0 6px 18px rgba(0,0,0,0.35);
    color: var(--ink);
  }
  .line-item {
    position: absolute;
    left: 0; right: 0;
    text-align: center;
    transform: translateY(-50%);
    white-space: nowrap;
  }

  .brand-name {
    top: 508px;
    font-family: "Josefin Sans", sans-serif;
    font-weight: 300;
    font-size: 64px;
    letter-spacing: 0.02em;
    display: flex;
    justify-content: center;
    align-items: center;
    gap: 18px;
  }
  .brand-dot { width: 12px; height: 12px; border-radius: 50%; background: var(--ink); display: inline-block; }

  .brand-sub {
    top: 581px;
    display: flex; justify-content: center; align-items: center; gap: 22px;
    font-family: "Poppins", sans-serif; font-weight: 300;
    font-size: 20px; letter-spacing: 0.32em;
  }
  .brand-sub .dash { width: 40px; height: 2px; background: var(--ink); display: inline-block; }

  .brand-motto {
    top: 624px;
    font-family: "Great Vibes", cursive;
    font-size: 20px;
    color: #4a5058;
  }

  .headline-serif {
    font-family: "Cormorant Garamond", serif;
    font-weight: 500;
    font-size: 124px;
    line-height: 1;
  }
  .headline-top { top: 727px; }
  .headline-mid { top: 817px; }
  .headline-script {
    top: 905px;
    font-family: "Great Vibes", cursive;
    font-size: 140px;
    line-height: 1;
  }

  .benefits {
    position: absolute;
    left: 246px;
    width: 408px;
    top: 976px;
    list-style: none;
    font-family: "Poppins", sans-serif;
    font-size: 18px;
    text-align: center;
  }
  .benefits li {
    height: 47.5px;
    line-height: 47.5px;
    border-bottom: 1px solid var(--rule);
  }
  .benefits li:last-child { border-bottom: none; }

  .product-type {
    top: 1255px;
    font-family: "Poppins", sans-serif;
    font-size: 23px;
    letter-spacing: 0.22em;
  }
  .product-size {
    top: 1297px;
    font-family: "Poppins", sans-serif;
    font-size: 23px;
  }

  .footer-mark { position: absolute; left: 0; top: 1340px; width: 900px; height: 40px; }
</style>
</head>
<body>
  <section class="label">
    <div class="line-item brand-name">CORVEL <span class="brand-dot"></span> MARE</div>
    <div class="line-item brand-sub"><span class="dash"></span>HANDMADE CANDLES<span class="dash"></span></div>
    <div class="line-item brand-motto">with purpose and love</div>

    <div class="line-item headline-serif headline-top">Elevate</div>
    <div class="line-item headline-serif headline-mid">Your</div>
    <div class="line-item headline-script">Ambiance</div>

    <ul class="benefits">
      <li>CLEAN-BURNING</li>
      <li>PARABEN-FREE</li>
      <li>PHTHALATE-FREE</li>
      <li>SKIN-SAFE</li>
      <li>PET-FRIENDLY</li>
    </ul>

    <div class="line-item product-type">COCONUT WAX CANDLE</div>
    <div class="line-item product-size">14 oz (596 gm)</div>

    <svg class="footer-mark" viewBox="0 0 900 40" aria-hidden="true">
      <line x1="217" y1="20" x2="396" y2="20" stroke="var(--ink)" stroke-width="1.5"/>
      <line x1="508" y1="20" x2="686" y2="20" stroke="var(--ink)" stroke-width="1.5"/>
      <circle cx="450" cy="20" r="9" fill="var(--ink)"/>
    </svg>
  </section>
</body>
</html>
```